Design Tolliver Stoneworks Core Values

We are a precast concrete manufacturing company that is looking to present (and eventually include in marketing) our core values to our employees (and eventually our customers). These values represent the morals, motivation and mission of our company. It is important to use these statements for evaluating performance and communicating who we are to both potential new-hires as well as new contractors.
Please design a graphic, hopefully using a product (or similar storm drain picture) image to organize the following:
TOLLIVER STONEWORKS CORE VALUES
1. We are committed to one another
• Coaching culture
• LMA (lead, manage, accountability)
• Employees win
• Zero 4 Ever
2. We know what our customers need
• Extensive experience
• Value engineering
• Excellent communication
3. We go the extra “yard”
• Follow up, follow through
• “Can do” attitude
• Do the little things well (Do the ordinary extraordinarily)

```html
<!DOCTYPE html>
<html lang="en">
<head>
<meta charset="utf-8">
<title>Tolliver Stoneworks Core Values</title>
<link href="https://fonts.googleapis.com/css2?family=Montserrat:ital,wght@0,300;0,400;0,800;0,900;1,300&family=Oswald:wght@500&display=swap" rel="stylesheet">
<style>
  :root{
    --concrete-light:#b9b9b7;
    --concrete-dark:#8f8f8d;
    --band:#33363a;
    --band-detail:#3e4246;
    --yellow:#e7dd55;
    --blue:#58d3e3;
    --green:#22d596;
    --ink:#0d0d0d;
    --text:#1c1c1c;
    --white:#ffffff;
  }
  *{margin:0;padding:0;box-sizing:border-box}
  html,body{width:854px;height:1200px;overflow:hidden}
  body{font-family:"Montserrat",sans-serif;color:var(--text)}
  .poster{
    position:relative;width:854px;height:1200px;overflow:hidden;
    background:radial-gradient(ellipse at 40% 30%,var(--concrete-light),var(--concrete-dark));
  }
  .backdrop{position:absolute;inset:0}
  .title{
    position:absolute;left:20px;top:12px;
    font-family:"Oswald",sans-serif;font-weight:500;font-size:42px;
    color:var(--white);letter-spacing:0;line-height:1.3;white-space:nowrap;
  }
  .brand{
    position:absolute;right:18px;top:118px;
    display:flex;align-items:center;gap:8px;
    font-weight:800;font-size:18px;color:var(--text);white-space:nowrap;
  }
  .brand-dot{width:14px;height:14px;border-radius:50%;background:var(--yellow)}
  .value{position:absolute}
  .numeral{
    position:absolute;font-weight:900;color:var(--ink);
    font-size:270px;line-height:1;letter-spacing:-6px;
  }
  .heading{
    position:absolute;font-weight:400;color:var(--ink);
    font-size:49px;line-height:53px;white-space:nowrap;
  }
  .points{position:absolute;list-style:none}
  .points li{
    position:relative;padding-left:22px;
    font-weight:300;font-size:28px;line-height:1.2;color:var(--text);white-space:nowrap;
  }
  .points li::before{
    content:"";position:absolute;left:2px;top:15px;width:8px;height:8px;border-radius:50%;background:var(--ink);
  }
  .note{font-style:italic;font-weight:300;font-size:18px;line-height:1.2;display:inline-block;vertical-align:middle}
</style>
</head>
<body>
<div class="poster">
  <svg class="backdrop" width="854" height="1200" viewBox="0 0 854 1200">
    <g class="product-bands">
      <rect x="0" y="740" width="854" height="48" fill="var(--band)"/>
      <rect x="0" y="800" width="854" height="80" fill="var(--band)"/>
      <rect x="0" y="894" width="854" height="78" fill="var(--band)"/>
      <rect x="0" y="988" width="854" height="132" fill="var(--band)"/>
    </g>
    <rect class="product-drawing" x="625" y="750" width="225" height="410" fill="var(--band-detail)" opacity="0.6" role="img" aria-label="Line drawing of a storm drain catch basin with riser and grate ring"/>
    <circle class="value-circle" cx="216" cy="376" r="272" fill="var(--yellow)" opacity="0.88"/>
    <circle class="value-circle" cx="616" cy="460" r="264" fill="var(--blue)" opacity="0.85"/>
    <circle class="value-circle" cx="284" cy="846" r="264" fill="var(--green)" opacity="0.85"/>
  </svg>

  <h1 class="title">TOLLIVER STONEWORKS CORE VALUES</h1>
  <div class="brand"><span class="brand-dot"></span>Tolliver Stoneworks</div>

  <section class="value value-one">
    <div class="numeral" style="left:14px;top:132px">1</div>
    <h2 class="heading" style="left:116px;top:152px">We are<br>committed<br>to one<br>another</h2>
    <ul class="points" style="left:30px;top:396px">
      <li style="margin-bottom:12px">Coaching culture</li>
      <li style="margin-bottom:10px">LMA <span class="note">(Lead, Manage,<br>Accountability)</span></li>
      <li style="margin-bottom:14px">Employees win</li>
      <li>Zero 4 Ever</li>
    </ul>
  </section>

  <section class="value value-two">
    <div class="numeral" style="left:404px;top:248px">2</div>
    <h2 class="heading" style="left:566px;top:280px">We know<br>what our<br>customers<br>need</h2>
    <ul class="points" style="left:424px;top:496px">
      <li style="margin-bottom:14px">Extensive experience</li>
      <li style="margin-bottom:14px">Value engineering</li>
      <li>Excellent communication</li>
    </ul>
  </section>

  <section class="value value-three">
    <div class="numeral" style="left:108px;top:620px">3</div>
    <h2 class="heading" style="left:270px;top:680px">We go<br>the extra<br>“yard”</h2>
    <ul class="points" style="left:80px;top:864px">
      <li style="margin-bottom:14px">Follow up, follow through</li>
      <li style="margin-bottom:14px">“Can do” attitude</li>
      <li>Do the little things well<br><span class="note" style="margin-left:-2px">(Do the ordinary extraordinarily)</span></li>
    </ul>
  </section>
</div>
</body>
</html>
```